Web Design for guards MMJ transport and security services

Harbor Crest Protective solutions a tallow unified company, is looking for a designer to create a website that displays our service portfolio. We need marketing pictures and content to be created in a original and competitive fashion, intriguing to our customers. We will need forms on the website to be created for calendar booking (somehow integrate into exchange if possible) and general inquiry forms. There will need to be pages dedicated to our staff, MMJ trasnport & Courier services, our vehicles, alarm systems, video systems, video monitoring, private investigations, and surveillance aduit and compliance investigations, payment gateway integration, and general company information. I Have attached our main company logo. Also have a emphasis on being state licensed by the Colorado RPB. Have a link to our parent site, tallowcctv.example

Target Market(s)

Colorado Marijuana industry, MMJ transport services, guard services, armed gaurd services.

Contact Information for Business Card

Would like a sleek simple design highlighting what we offer. must match the website and have a overall professional straight to the point appearance.

Number of Pages Required

1 page

Colors
33b8a4
00a990
9bcb3c
acd036
cadf82
85cae6
33a6d7
0792cd

Requirements
Must have
• Easy to use, lots of images, professional.
Nice to have
• Creativity

```html
<!DOCTYPE html>
<html lang="en">
<head>
<meta charset="utf-8">
<title>Harbor Crest Protective Solutions</title>
<link href="https://fonts.googleapis.com/css2?family=Open+Sans:wght@400;600;700&display=swap" rel="stylesheet">
<style>
:root{
  --teal:#00a990;
  --teal-soft:#33b8a4;
  --teal-ring:#2cc0a8;
  --lime:#9bcb3c;
  --dark:#0e3a33;
  --darker:#0a2f29;
  --ink:#1d1d1d;
  --muted:#6f6f6f;
  --light-muted:#9a9a9a;
  --white:#ffffff;
  --red:#d42a2a;
}
*{box-sizing:border-box;margin:0;padding:0}
html,body{width:1200px;height:2287px;overflow:hidden;background:var(--white);font-family:"Open Sans",Arial,sans-serif;color:var(--ink)}
.page{position:relative;width:1200px;height:2287px}
.abs{position:absolute}

/* header */
.site-header{position:absolute;left:0;top:0;width:1200px;height:131px;background:var(--white);border-bottom:2px solid #d8d8d8}
.brand{position:absolute;left:110px;top:22px;width:140px;display:flex;flex-direction:column;align-items:center;gap:8px}
.brand-mark{width:64px;height:64px;border-radius:50%;background:var(--red)}
.brand-name{font-size:17px;font-weight:700;color:var(--red)}
.top-contact{position:absolute;top:40px;font-size:12px;color:#333;display:flex;align-items:center;gap:8px}
.main-nav{position:absolute;top:98px;left:0;width:1200px;font-size:12.5px;font-weight:700;color:#222}
.main-nav span{position:absolute;white-space:nowrap}
.nav-active-bar{position:absolute;left:392px;top:125px;width:60px;height:6px;background:var(--teal)}

/* hero */
.hero{position:absolute;left:0;top:131px;width:1200px;height:471px;background:linear-gradient(115deg,#3e5567 0%,#6f8596 35%,#9aabb9 55%,#4f6577 80%,#2f4353 100%)}
.hero-title{position:absolute;left:108px;top:300px;font-size:52px;font-weight:600;color:var(--white);letter-spacing:1px}
.hero-text{position:absolute;left:112px;top:374px;width:460px;font-size:12px;line-height:25px;color:var(--white)}
.hero-arrows{position:absolute;left:112px;top:438px}

/* features band */
.features{position:absolute;left:0;top:602px;width:1200px;height:225px;background:var(--teal)}
.feature-circle{position:absolute;width:180px;height:180px;border-radius:50%;background:var(--teal);border:3px solid var(--teal-ring);top:513px;display:flex;align-items:flex-start;justify-content:center;padding-top:40px}
.feature-title{position:absolute;top:645px;width:340px;text-align:center;font-size:20px;font-weight:700;color:var(--white)}
.feature-rule{position:absolute;top:686px;width:80px;height:1px;background:rgba(255,255,255,.45)}
.feature-text{position:absolute;top:706px;width:290px;text-align:justify;text-align-last:center;font-size:11.5px;line-height:26px;color:var(--white)}

/* welcome */
.welcome-heading{position:absolute;left:0;top:938px;width:1200px;text-align:center;font-size:26px;font-weight:700;color:var(--ink)}
.welcome-heading em{font-style:normal;color:var(--teal)}
.welcome-text{position:absolute;left:115px;top:988px;width:970px;text-align:center;font-size:11.5px;line-height:31px;color:var(--muted)}

/* services */
.services-bar{position:absolute;left:0;top:1120px;width:1200px;height:75px;background:var(--teal);color:var(--white);font-size:25px;font-weight:700;text-align:center;line-height:75px}
.services-body{position:absolute;left:0;top:1195px;width:1200px;height:481px;background:linear-gradient(135deg,#0f4139 0%,#0b3630 60%,#0d3b34 100%)}
.tab-strip{position:absolute;left:111px;top:1195px;width:978px;height:67px;background:var(--darker)}
.tab-active-bg{position:absolute;left:111px;top:1195px;width:290px;height:67px;background:#123e37;clip-path:polygon(0 0,100% 0,86% 100%,0 100%)}
.tab{position:absolute;top:1218px;font-size:14.5px;font-weight:700;color:var(--white)}
.tab-underline{position:absolute;left:196px;top:1244px;width:147px;height:2px;background:var(--lime)}
.card{position:absolute;top:1305px;width:226px;height:325px;background:var(--white)}
.card-photo{width:226px;height:145px}
.card-title{position:absolute;left:21px;top:166px;font-size:13px;font-weight:600;color:#222}
.card-text{position:absolute;left:21px;top:193px;width:186px;font-size:10.5px;line-height:25px;color:var(--muted);text-align:justify}
.card-link{position:absolute;left:21px;top:281px;font-size:11px;font-weight:600;color:var(--teal)}

/* news */
.section-heading{position:absolute;top:1732px;font-size:25px;font-weight:700;color:var(--ink)}
.section-heading em{font-style:normal;color:var(--teal)}
.news-photo-frame{position:absolute;left:110px;top:1790px;width:216px;height:146px;border:1px solid #ddd;padding:3px}
.news-photo{width:100%;height:100%;background:linear-gradient(160deg,#d7d7d7,#b9bdc0)}
.news-date{position:absolute;left:4px;bottom:4px;width:206px;height:40px;background:var(--teal);color:var(--white);font-size:11.5px;text-align:center;line-height:40px}
.news-lead{position:absolute;left:349px;top:1783px;width:312px;font-size:12.5px;line-height:30px;color:#333}
.news-body{position:absolute;left:349px;top:1850px;width:312px;font-size:11.5px;line-height:28px;color:var(--light-muted);text-align:justify}
.partner-text{position:absolute;left:697px;top:1783px;width:392px;font-size:12.5px;line-height:30px;color:#333}
.partner-name{position:absolute;left:706px;top:1870px;font-size:24px;font-weight:600;color:#2a8fc4;display:flex;align-items:center;gap:10px}
.partner-dot{width:40px;height:40px;border-radius:50%;background:#2a8fc4}
.partner-badge{position:absolute;left:925px;top:1858px;width:66px;height:66px;border-radius:50%;background:#3a3a2a;border:3px solid #c9a633}

/* footer */
.site-footer{position:absolute;left:0;top:1995px;width:1200px;height:208px;background:var(--teal);color:var(--white)}
.footer-heading{position:absolute;top:2024px;font-size:15px;font-weight:700;color:var(--white)}
.footer-divider{position:absolute;top:2022px;width:1px;height:160px;background:rgba(255,255,255,.25)}
.footer-line{position:absolute;font-size:11.5px;color:var(--white);white-space:nowrap}
.avatar{position:absolute;left:578px;top:2113px;width:50px;height:50px;border-radius:50%;background:linear-gradient(#b79b77,#7c6a52);border:3px solid #d9eee9}
.bottom-bar{position:absolute;left:0;top:2203px;width:1200px;height:84px;background:var(--darker);color:var(--white);font-size:11.5px}
.social{position:absolute;top:2232px;width:22px;height:22px}
</style>
</head>
<body>
<div class="page">

  <header class="site-header">
    <div class="brand">
      <div class="brand-mark"></div>
      <div class="brand-name">Harbor Crest</div>
    </div>
    <div class="top-contact" style="left:666px">
      <svg width="12" height="18" viewBox="0 0 12 18"><rect x="1" y="1" width="10" height="16" rx="2" fill="none" stroke="#9bcb3c" stroke-width="1.6"/><circle cx="6" cy="14" r="1" fill="#9bcb3c"/></svg>
      CALL US : 123 456 7890
    </div>
    <div class="top-contact" style="left:842px">
      <svg width="18" height="14" viewBox="0 0 18 14"><rect x="1" y="1" width="16" height="12" fill="none" stroke="#9bcb3c" stroke-width="1.6"/><path d="M1 1 9 8 17 1" fill="none" stroke="#9bcb3c" stroke-width="1.6"/></svg>
      EMAIL US : INFO@HARBORCREST.EXAMPLE
    </div>
    <nav class="main-nav">
      <span style="left:401px">HOME</span>
      <span style="left:496px">ABOUT US</span>
      <span style="left:616px">OUR STAFF</span>
      <span style="left:740px">SERVICES
        <svg width="8" height="6" viewBox="0 0 8 6" style="margin-left:5px"><path d="M1 1 4 4 7 1" fill="none" stroke="#222" stroke-width="1.4"/></svg></span>
      <span style="left:868px">OUR VEHICLES</span>
      <span style="left:1013px">CONTACT US</span>
    </nav>
    <div class="nav-active-bar"></div>
  </header>

  <section class="hero" role="img" aria-label="Security camera mounted on a building facade"></section>
  <h1 class="hero-title">SAFE &amp; SECURE</h1>
  <p class="hero-text">Lorem ipsum dolor sit amet, consectetur adipiscing elit. Morbi vel aliquet eros. Sed sodales, libero in molestie convallis, sapien lorem scelerisque enim.</p>
  <svg class="hero-arrows" width="50" height="24" viewBox="0 0 50 24"><path d="M13 3 5 12 13 21" fill="none" stroke="#fff" stroke-width="4"/><path d="M33 3 41 12 33 21" fill="none" stroke="#fff" stroke-width="4"/></svg>

  <section class="features"></section>
  <div class="feature-circle" style="left:177px">
    <svg width="80" height="54" viewBox="0 0 80 54"><g fill="none" stroke="#fff" stroke-width="2.5"><rect x="22" y="6" width="30" height="30"/><path d="M52 16h14l10 12v8H52"/><circle cx="32" cy="42" r="6"/><circle cx="64" cy="42" r="6"/><path d="M2 14h14M6 22h12M2 30h14"/></g></svg>
  </div>
  <div class="feature-circle" style="left:509px">
    <svg width="60" height="66" viewBox="0 0 60 66"><path d="M30 3 55 12v20c0 16-11 27-25 31C16 59 5 48 5 32V12Z" fill="none" stroke="#fff" stroke-width="3"/><path d="M20 32h6v14h-6zM26 44h12c3 0 4-2 4-4l2-8c0-2-1-3-3-3h-8l1-6c0-3-3-4-4-1l-4 8" fill="none" stroke="#fff" stroke-width="2.5" stroke-linejoin="round"/></svg>
  </div>
  <div class="feature-circle" style="left:845px">
    <svg width="70" height="56" viewBox="0 0 70 56"><g fill="none" stroke="#fff" stroke-width="2.5"><circle cx="26" cy="16" r="12"/><path d="M4 52c0-14 10-22 22-22s22 8 22 22Z"/><circle cx="48" cy="20" r="9"/><path d="M46 33c12 0 20 6 20 19H50"/></g></svg>
  </div>
  <div class="feature-title" style="left:97px">TRANSPORT</div>
  <div class="feature-rule" style="left:227px"></div>
  <p class="feature-text" style="left:122px">Fusce finibus ante risus, in efficitur lacus semper ac. Sed leo urna, facilisis vitae imperdiet et, rutrum et turpis.</p>
  <div class="feature-title" style="left:429px">SECURITY</div>
  <div class="feature-rule" style="left:559px"></div>
  <p class="feature-text" style="left:454px">Duis vel mattis ex. Duis eget quam in mi tincidunt posuere. Etiam nulla lorem, condimentum vitae massa vel, venenatis gravida nunc.</p>
  <div class="feature-title" style="left:765px">OUR STAFFS</div>
  <div class="feature-rule" style="left:895px"></div>
  <p class="feature-text" style="left:790px">Lorem ipsum dolor sit amet, consectetur adipiscing elit. Morbi vel aliquet eros. Sed sodales, libero in molestie convallis.</p>

  <svg class="abs" style="left:570px;top:864px" width="60" height="66" viewBox="0 0 60 66"><path d="M30 3 55 12v20c0 16-11 27-25 31C16 59 5 48 5 32V12Z" fill="none" stroke="#9bcb3c" stroke-width="4"/></svg>
  <h2 class="welcome-heading">WELCOME TO <em>HARBOR CREST PROTECTIVE SOLUTIONS</em></h2>
  <p class="welcome-text">Morbi lobortis nisi a ultrices rhoncus. Nunc efficitur turpis mi, a aliquam mi facilisis et. Fusce nulla tortor, consectetur vitae suscipit non, hendrerit non arcu. Sed vitae feugiat velit. Morbi id venenatis nisi. Mauris feugiat malesuada tempus. Curabitur hendrerit egestas velit vitae convallis. In ut tincidunt purus. Pellentesque non orci nisi. Vestibulum quis enim convallis, dapibus massa in, suscipit quam. Aliquam vitae fermentum lorem.</p>

  <div class="services-bar">OUR SERVICES</div>
  <section class="services-body"></section>
  <div class="tab-strip"></div>
  <div class="tab-active-bg"></div>
  <div class="tab" style="left:196px">SECURITY SERVICES</div>
  <div class="tab-underline"></div>
  <div class="tab" style="left:445px">TRANSPORT SERVICES</div>

  <article class="card" style="left:111px">
    <div class="card-photo" role="img" aria-label="Red alarm bell on a wall" style="background:linear-gradient(135deg,#e4e4e4,#b7b7b7 60%,#c33 61%,#9c1c1c)"></div>
    <h3 class="card-title">ALARM SYSTEMS</h3>
    <p class="card-text">Lorem ipsum dolor sit amet, con sectetur adipiscing elit. Morbi v zel aliquet eros.</p>
    <div class="card-link">&#10070; READ MORE</div>
  </article>
  <article class="card" style="left:361px">
    <div class="card-photo" role="img" aria-label="Dome security camera on a concrete ceiling" style="background:linear-gradient(150deg,#e6e6e6,#c4c4c4)"></div>
    <h3 class="card-title">VIDEO SYSTEMS</h3>
    <p class="card-text">Morbi id venenatis nisi. Mauris fe ugiat malesuada tempus. Cur abitur hendrerit egestas.</p>
    <div class="card-link">&#10070; READ MORE</div>
  </article>
  <article class="card" style="left:613px">
    <div class="card-photo" role="img" aria-label="Investigator examining documents with a magnifying glass" style="background:linear-gradient(160deg,#8db3d9,#dfe4ea 60%,#f2f2f2)"></div>
    <h3 class="card-title">PRIVATE INVESTIGATIONS</h3>
    <p class="card-text">Lorem ipsum dolor sit amet, con sectetur adipiscing elit. Morbi v zel aliquet eros.</p>
    <div class="card-link">&#10070; READ MORE</div>
  </article>
  <article class="card" style="left:863px">
    <div class="card-photo" role="img" aria-label="Business person touching a digital surveillance display" style="background:linear-gradient(135deg,#6b6b6b,#9d9d9d 55%,#4a4a4a)"></div>
    <h3 class="card-title">SURVEILLANCE AUDIT</h3>
    <p class="card-text">Morbi id venenatis nisi. Mauris fe ugiat malesuada tempus. Cur abitur hendrerit egestas.</p>
    <div class="card-link">&#10070; READ MORE</div>
  </article>

  <h2 class="section-heading" style="left:110px">LATEST <em>NEWS</em></h2>
  <svg class="abs" style="left:618px;top:1740px" width="46" height="22" viewBox="0 0 46 22"><path d="M11 3 4 11 11 19" fill="none" stroke="#222" stroke-width="3.5"/><path d="M35 3 42 11 35 19" fill="none" stroke="#222" stroke-width="3.5"/></svg>
  <div class="news-photo-frame">
    <div class="news-photo" role="img" aria-label="Hand entering a code on an alarm keypad"></div>
    <div class="news-date">MAR 10 ,2016</div>
  </div>
  <p class="news-lead">Lorem ipsum dolor sit amet, consectetur adipiscing elit. Morbi vel aliquet eros.</p>
  <p class="news-body">Aliquam imperdiet erat sit amet ipsum elementum viverra. Sed finibus commodo nibh accumsan vehicula. Morbi vitae lobortis magna.</p>

  <h2 class="section-heading" style="left:697px">WE <em>WORK WITH</em></h2>
  <p class="partner-text">Duis eget quam in mi tincidunt posuere. Etiam nulla lorem, con dimentum vitae massa vel, venenatis gravida nunc.</p>
  <div class="partner-name"><span class="partner-dot"></span>tallow unified</div>
  <div class="partner-badge"></div>

  <footer class="site-footer"></footer>
  <div class="footer-heading" style="left:110px">CONTACT US</div>
  <svg class="abs" style="left:115px;top:2057px" width="10" height="14" viewBox="0 0 10 14"><path d="M5 13C1 8 1 6 1 5a4 4 0 0 1 8 0c0 1 0 3-4 8Z" fill="#9bcb3c"/></svg>
  <div class="footer-line" style="left:134px;top:2056px">HARBOR CREST</div>
  <div class="footer-line" style="left:134px;top:2075px;line-height:20px">4623 Lorem Ipsm, Lorem Ipsm<br>Lorem Ipsm 95356</div>
  <svg class="abs" style="left:111px;top:2120px" width="16" height="12" viewBox="0 0 16 12"><rect width="16" height="12" fill="#9bcb3c"/><path d="M1 1 8 7 15 1" fill="none" stroke="#00a990" stroke-width="1.5"/></svg>
  <div class="footer-line" style="left:136px;top:2118px">info@harborcrest.example</div>
  <svg class="abs" style="left:111px;top:2153px" width="15" height="15" viewBox="0 0 15 15"><rect width="15" height="15" fill="#9bcb3c"/><path d="M4 3c0 5 3 8 8 9l1-2-2-2-2 1c-1-1-2-2-3-3l1-2-2-2Z" fill="#00a990"/></svg>
  <div class="footer-line" style="left:138px;top:2152px">888-555-0142</div>

  <div class="footer-divider" style="left:337px"></div>
  <div class="footer-heading" style="left:384px">QUICK LINKS</div>
  <div class="footer-line" style="left:386px;top:2056px">About us</div>
  <div class="footer-line" style="left:386px;top:2082px">Services</div>
  <div class="footer-line" style="left:386px;top:2107px">Our vehicles</div>
  <div class="footer-line" style="left:386px;top:2133px">Blog</div>
  <div class="footer-line" style="left:386px;top:2158px">Contact Us</div>

  <div class="footer-divider" style="left:533px"></div>
  <div class="footer-heading" style="left:577px">TESTIMONIALS</div>
  <svg class="abs" style="left:1054px;top:2026px" width="36" height="16" viewBox="0 0 36 16"><path d="M8 2 3 8 8 14" fill="none" stroke="#fff" stroke-width="3"/><path d="M28 2 33 8 28 14" fill="none" stroke="#fff" stroke-width="3"/></svg>
  <p class="footer-line" style="left:577px;top:2060px;width:512px;white-space:normal;line-height:26px">Nullam auctor neque nec tortor sagittis congue. Aliquam est metus, ornare a dictum id, finibus eget urna. Sed laoreet lacus vitae sapien bibendum sodales.</p>
  <div class="avatar" role="img" aria-label="Client portrait"></div>
  <div class="footer-line" style="left:638px;top:2122px;font-size:14px">- Lena Marsh</div>
  <div class="footer-line" style="left:647px;top:2145px;font-size:11px">Location</div>

  <div class="bottom-bar"></div>
  <div class="footer-line" style="left:110px;top:2235px">Copyright © 2016 Harbor Crest Protective solutions. All Rights Reserved. <span style="color:#cadf82;margin-left:10px">Privacy Policy</span><span style="color:#cadf82;margin-left:10px">Terms of Service</span></div>
  <div class="social" style="left:971px;background:#3b5a9a"></div>
  <div class="social" style="left:1003px;background:#2a9fd6"></div>
  <div class="social" style="left:1035px;background:#d2432f"></div>
  <div class="social" style="left:1067px;background:#e8912a"></div>

</div>
</body>
</html>
```